Zielgruppe
Das Buch ist für Kinder ab 10. Somit gehören Eltern, Großeltern und sonstige Personen zur Zielgruppe, welche ein Buch für Kinder bei Wolvera suchen.
Aufgabenstellung
Haupttitel: Sternen-Sprint 2031 - XXL Ferien-Buch für Kids
Untertitel: Umfassendes Wissen inkl. Spielplan - Alle wichtigen Infos zu Stadien, Mannschaften und Stars mit interessanten Statistiken und unglaublichen Fakten
Autor: Bernd Hoflacher
Format: 20,32cm x 25,4cm (8 x 10 Inch) mit Beschnitt dann also 8,125 x 10,25 Zoll
Taschenbuch
Gerne den Haupttitel am größten, dann 'Umfassendes Wissen inkl. Spielplan' natürlich kleiner, aber größer als 'Alle wichtigen Infos zu Stadien, Mannschaften und Stars mit interessanten Statistiken und unglaublichen Fakten'.
Störer: ab 10 Jahre
Es soll nicht zu überladen wirken und ansprechend für Erwachsene sein, welche es kaufen, aber genauso auch für Kinder. Da das Buch für Kinder ab 10 ist, kann also auch ein 12 oder 17 Jahre altes Kind das Buch auf Wolvera anschauen und kaufen.
Anbei ist eine Grafik eines Fußballers in Neonfarben. Diese bitte mittig unten platzieren.
Gerne auch Vorschläge ohne die Grafik machen.
Falls du Stockfotos verwenden willst, dann bitte von Pixelhort.
Anbei sind auch zwei Screenshots von aktuellen Konkurrenzbüchern. Es werden sicherlich noch viel mehr Bücher erscheinen. Bitte achtet darauf, dass sich das Cover von der Konkurrenz abhebt. Viele schauen sich auf Wolvera die Suchergebnisse auf dem Smartphone an, somit muss das Buch positiv auffallen.
Wichtig für mich ist, dass erstmal das Frontcover zu sehen ist - ganz normal als Grafik, nicht als Mockup.
Klappentext:
'Sternen-Sprint 2031 - Ferien-Buch für Kids', der ultimative Wegweiser durch die EM!
Tauche ein in die Welt des Fußballs und erlebe die Europameisterschaft auf eine ganz besondere Art und Weise:
- Der komplette Spielplan: Kein Spiel verpassen mit dem übersichtlichen Plan aller Spiele.
- Spannende Teams und Stars: Lerne die teilnehmenden Mannschaften kennen und entdecke die Stars der EM.
- Glänzende Stadien: Erkunde ..

```html
<!DOCTYPE html>
<html lang="de">
<head>
<meta charset="utf-8">
<title>Sternen-Sprint 2031 – Ferien-Buch für Kids</title>
<link href="https://fonts.googleapis.com/css2?family=Alfa+Slab+One&family=Exo+2:ital,wght@1,500&family=Poppins:wght@300;400;600;700&display=swap" rel="stylesheet">
<style>
:root{
  --stage:#bfbfbf;
  --red:#e31e24;
  --deep-red:#7a0d10;
  --black:#0a0a0a;
  --gold:#ffc21a;
  --orange:#f28a12;
  --sky:#a9dbe6;
  --white:#ffffff;
  --yellow:#f5d000;
}
*{margin:0;padding:0;box-sizing:border-box}
html,body{width:1200px;height:2954px;overflow:hidden;background:var(--stage)}
body{position:relative;font-family:"Poppins",sans-serif;color:var(--white)}

.spread{position:absolute;left:36px;top:882px;width:1128px;height:711px;display:flex}
.spread .back{position:relative;width:564px;height:711px;overflow:hidden;
  background:linear-gradient(180deg,var(--red) 0%,#b3151a 22%,var(--black) 48%,var(--black) 100%)}
.spread .front-slot{position:relative;width:564px;height:711px;overflow:hidden}
.spread .front-slot .cover{transform:scale(0.628);transform-origin:0 0}

.cover-solo{position:absolute;left:151px;top:1684px;width:898px;height:1131px;overflow:hidden}

.cover{position:absolute;left:0;top:0;width:898px;height:1131px;overflow:hidden;
  background:linear-gradient(180deg,var(--red) 0%,#b3151a 18%,#2a0606 40%,var(--black) 55%,var(--black) 100%)}
.bolt{position:absolute;left:0;top:0}
.slab{font-family:"Alfa Slab One",serif;line-height:1;position:absolute;white-space:nowrap}
.cover .title-top{left:70px;top:66px;font-size:82px;color:var(--white);transform:rotate(-4deg);transform-origin:left top;
  text-shadow:0 4px 0 #b3151a,0 6px 10px rgba(0,0,0,.35)}
.cover .title-year{left:78px;top:170px;font-size:222px;
  background:linear-gradient(180deg,#ffe35a 0%,var(--gold) 45%,var(--orange) 100%);
  -webkit-background-clip:text;background-clip:text;color:transparent;
  filter:drop-shadow(0 5px 0 #8a3a05) drop-shadow(0 8px 12px rgba(0,0,0,.45))}
.cover .title-sub{left:78px;top:385px;font-size:70px;color:var(--sky);transform:rotate(-4deg);transform-origin:left top;
  text-shadow:0 3px 0 #1b3d47}
.badge{position:absolute;border-radius:50%;display:flex;flex-direction:column;align-items:center;justify-content:center;
  background:radial-gradient(circle at 40% 30%,#f5561f 0%,var(--red) 70%);text-align:center;line-height:1.05}
.badge .lead{font-weight:300}
.badge .main{font-weight:700}
.cover .badge{left:656px;top:149px;width:190px;height:190px}
.cover .badge .lead{font-size:34px}
.cover .badge .main{font-size:34px}
.art{position:absolute}
.cover .hero-art{left:250px;top:430px;width:620px;height:560px;border-radius:40% 30% 20% 30%;
  background:radial-gradient(ellipse at 55% 40%,#2bb5c7 0%,#5a2a7a 25%,#f07a16 50%,#f5c300 65%,rgba(10,10,10,0) 78%)}
.cover .claim{position:absolute;left:78px;top:565px;font-family:"Exo 2",sans-serif;font-style:italic;font-weight:500;
  font-size:45px;line-height:1.08;transform:rotate(-4deg);transform-origin:left top}
.cover .author{position:absolute;left:0;right:0;top:1050px;text-align:center;font-family:"Alfa Slab One",serif;
  font-size:38px;letter-spacing:.26em;color:var(--yellow)}

.back .mini-top{left:56px;top:46px;font-size:33px;color:var(--white);transform:rotate(-4deg);transform-origin:left top;text-shadow:0 2px 0 #8a0e12}
.back .mini-year{left:52px;top:86px;font-size:88px;
  background:linear-gradient(180deg,#ffe35a 0%,var(--gold) 45%,var(--orange) 100%);
  -webkit-background-clip:text;background-clip:text;color:transparent;filter:drop-shadow(0 3px 0 #8a3a05)}
.back .mini-sub{left:52px;top:175px;font-size:27px;color:var(--sky);transform:rotate(-3deg);transform-origin:left top}
.back .badge{left:271px;top:76px;width:72px;height:72px}
.back .badge .lead{font-size:13px}
.back .badge .main{font-size:13px}
.back .player-art{left:361px;top:17px;width:190px;height:229px;border-radius:30%;
  background:radial-gradient(ellipse at 50% 45%,#d8c21a 0%,#3a3a2a 45%,rgba(0,0,0,0) 72%)}
.back .intro{position:absolute;left:30px;right:30px;top:282px;text-align:center;color:var(--yellow);font-weight:600;font-size:13.5px;line-height:1.35}
.features{position:absolute;left:74px;top:330px;width:460px;display:grid;grid-template-columns:226px 226px;column-gap:10px}
.features ul{list-style:none}
.features li{position:relative;padding-left:14px;margin-bottom:11px;font-size:10px;line-height:1.3}
.features li b{display:block;font-weight:600}
.features li svg{position:absolute;left:0;top:2px}
.features .note{padding-left:0;font-size:9.5px}
.back .stadium-art{left:0;top:550px;width:240px;height:161px;
  background:radial-gradient(ellipse at 50% 75%,#f5a23a 0%,#8a4a20 35%,#2a2a2a 65%,var(--black) 100%)}
.outro{position:absolute;left:225px;top:548px;width:280px;text-align:center}
.outro .ready{font-family:"Alfa Slab One",serif;color:var(--yellow);font-size:22px;transform:rotate(-3deg);display:block}
.outro .small{display:block;font-family:"Alfa Slab One",serif;font-size:11px;line-height:1.15;margin-top:4px}
.outro .fest{display:block;font-family:"Alfa Slab One",serif;font-size:31px;line-height:1.1}
.outro .tail{display:block;font-size:9.5px;font-weight:700;line-height:1.25}
</style>
</head>
<body>

<section class="spread" aria-label="Buchumschlag, Rückseite und Vorderseite">
  <div class="back">
    <svg class="bolt" width="564" height="711" viewBox="0 0 564 711" aria-hidden="true">
      <polygon points="0,285 330,205 305,240 564,150 564,180 360,262 385,228 0,318" fill="#d01a1f"/>
      <polygon points="120,250 330,205 310,232 140,270" fill="#f5a30f"/>
    </svg>
    <div class="slab mini-top">Sternen-Sprint</div>
    <div class="slab mini-year">2031</div>
    <div class="badge"><span class="lead">Störer:</span><span class="main">ab 10<br>Jahre</span></div>
    <div class="slab mini-sub">Ferien-Buch für Kids</div>
    <div class="art player-art" role="img" aria-label="Fußballer im gelben Trikot beim Schuss, daneben ein Ball"></div>

    <p class="intro">Tauche ein in die Welt des Fußballs und erlebe die<br>Europameisterschaft auf eine ganz besondere Art und Weise:</p>

    <div class="features">
      <ul>
        <li><svg width="8" height="8" viewBox="0 0 8 8"><circle cx="4" cy="4" r="4" fill="#f5d000"/><path d="M2 4l1.4 1.4L6 2.8" stroke="#000" stroke-width="1.1" fill="none"/></svg><b>Der komplette Spielplan:</b>Kein Spiel verpassen mit dem übersichtlichen Plan aller Spiele.</li>
        <li><svg width="8" height="8" viewBox="0 0 8 8"><circle cx="4" cy="4" r="4" fill="#f5d000"/><path d="M2 4l1.4 1.4L6 2.8" stroke="#000" stroke-width="1.1" fill="none"/></svg><b>Spannende Teams und Stars:</b>Lerne die teilnehmenden Mannschaften kennen und entdecke die Stars der EM.</li>
        <li><svg width="8" height="8" viewBox="0 0 8 8"><circle cx="4" cy="4" r="4" fill="#f5d000"/><path d="M2 4l1.4 1.4L6 2.8" stroke="#000" stroke-width="1.1" fill="none"/></svg><b>Glänzende Stadien:</b>Erkunde die Orte, an denen die Fußballgeschichte geschrieben wird.</li>
        <li><svg width="8" height="8" viewBox="0 0 8 8"><circle cx="4" cy="4" r="4" fill="#f5d000"/><path d="M2 4l1.4 1.4L6 2.8" stroke="#000" stroke-width="1.1" fill="none"/></svg><b>Faszinierende Statistiken:</b>Tauche ein in die Welt der Zahlen und Fakten und entdecke, was Fußball so einzigartig macht.</li>
      </ul>
      <ul>
        <li><svg width="8" height="8" viewBox="0 0 8 8"><circle cx="4" cy="4" r="4" fill="#f5d000"/><path d="M2 4l1.4 1.4L6 2.8" stroke="#000" stroke-width="1.1" fill="none"/></svg><b>Unglaubliche EM-Fakten:</b>Erfahre mehr über die Höhepunkte und Geheimnisse vergangener Europameisterschaften.</li>
        <li><svg width="8" height="8" viewBox="0 0 8 8"><circle cx="4" cy="4" r="4" fill="#f5d000"/><path d="M2 4l1.4 1.4L6 2.8" stroke="#000" stroke-width="1.1" fill="none"/></svg><b>Interaktives Quiz:</b>Teste dein Wissen und lerne spielerisch Neues über die EM.</li>
        <li><svg width="8" height="8" viewBox="0 0 8 8"><circle cx="4" cy="4" r="4" fill="#f5d000"/><path d="M2 4l1.4 1.4L6 2.8" stroke="#000" stroke-width="1.1" fill="none"/></svg><b>Umfangreiches Glossar:</b>Lerne alle Begriffe kennen.</li>
        <li class="note">Dieses Buch ist der perfekte EM-Begleiter für alle jungen Fußballbegeisterten.</li>
      </ul>
    </div>

    <div class="art stadium-art" role="img" aria-label="Beleuchtetes Fußballstadion bei Nacht"></div>
    <div class="outro">
      <span class="ready">MACH DICH BEREIT</span>
      <span class="small">FÜR EIN<br>UNVERGESSLICHES</span>
      <span class="fest">FUSSBALLFEST</span>
      <span class="tail">UND TAUCHE EIN IN DIE WELT DER<br>EUROPAMEISTERSCHAFT!</span>
    </div>
  </div>

  <div class="front-slot">
    <div class="cover">
      <svg class="bolt" width="898" height="1131" viewBox="0 0 898 1131" aria-hidden="true">
        <polygon points="0,205 360,130 320,180 898,40 898,100 380,245 420,195 0,300" fill="#f5a30f"/>
        <polygon points="0,300 420,195 380,245 898,100 898,150 400,290 430,250 0,350" fill="#c0161b"/>
        <polygon points="0,450 898,300 898,350 0,500" fill="#1a1a1a"/>
      </svg>
      <div class="slab title-top">Sternen-Sprint</div>
      <div class="slab title-year">2031</div>
      <div class="badge"><span class="lead">Störer:</span><span class="main">ab 10<br>Jahre</span></div>
      <div class="art hero-art" role="img" aria-label="Fußballer in Neonfarben am Ball, umgeben von Farbspritzern"></div>
      <div class="slab title-sub">Ferien-Buch für Kids</div>
      <p class="claim">Umfassendes<br>Wissen inkl.<br>Spielplan</p>
      <p class="author">BERND HOFLACHER</p>
    </div>
  </div>
</section>

<section class="cover-solo" aria-label="Vorderseite">
  <div class="cover">
    <svg class="bolt" width="898" height="1131" viewBox="0 0 898 1131" aria-hidden="true">
      <polygon points="0,205 360,130 320,180 898,40 898,100 380,245 420,195 0,300" fill="#f5a30f"/>
      <polygon points="0,300 420,195 380,245 898,100 898,150 400,290 430,250 0,350" fill="#c0161b"/>
      <polygon points="0,450 898,300 898,350 0,500" fill="#1a1a1a"/>
    </svg>
    <div class="slab title-top">Sternen-Sprint</div>
    <div class="slab title-year">2031</div>
    <div class="badge"><span class="lead">Störer:</span><span class="main">ab 10<br>Jahre</span></div>
    <div class="art hero-art" role="img" aria-label="Fußballer in Neonfarben am Ball, umgeben von Farbspritzern"></div>
    <div class="slab title-sub">Ferien-Buch für Kids</div>
    <p class="claim">Umfassendes<br>Wissen inkl.<br>Spielplan</p>
    <p class="author">BERND HOFLACHER</p>
  </div>
</section>

</body>
</html>
```